Redesign of business card for Cedar Ridge Mechanical

We are looking for a new design for our business cards for Cedar Ridge Mechanical. We are a plumbing & HVAC construction company, operating on the West Coast of Canada and USA. Logo attached.
Industry/Entity Type
Construction - Plumbing & HVAC
Contact Information for Business Card
Name, address, phone numbers, email, website address
Look and feel
Each slider illustrates characteristics of the customer's brand and the style your logo design should communicate.

```html
<!DOCTYPE html>
<html lang="en">
<head>
<meta charset="utf-8">
<title>Cedar Ridge Mechanical – Business Card</title>
<link href="https://fonts.googleapis.com/css2?family=Oswald:wght@500;700&family=Arimo:wght@400&display=swap" rel="stylesheet">
<style>
  :root {
    --slate: #454f63;
    --slate-dark: #363e4f;
    --slate-light: #5a6479;
    --silver: #b9bcc2;
    --paper: #ffffff;
    --stage: #e6e7ea;
    --ink-soft: #4b5467;
  }
  * { box-sizing: border-box; margin: 0; padding: 0; }
  html, body { width: 1200px; height: 875px; overflow: hidden; }
  body {
    background: var(--stage);
    font-family: "Arimo", Arial, sans-serif;
    display: flex;
    flex-direction: column;
    align-items: center;
    justify-content: center;
    gap: 40px;
  }
  .card {
    position: relative;
    width: 665px;
    height: 380px;
    border-radius: 22px;
    overflow: hidden;
    box-shadow: 0 10px 28px rgba(0,0,0,0.18);
  }

  /* Back of card */
  .card-back {
    background: var(--slate);
  }
  .card-back .pattern-area {
    position: absolute;
    inset: 0;
    background: linear-gradient(120deg, var(--slate-light) 0%, var(--slate) 45%, var(--slate-dark) 100%);
  }
  .card-back .back-brand {
    position: absolute;
    left: 50%;
    top: 50%;
    transform: translate(-50%, -50%);
    display: flex;
    align-items: center;
    gap: 12px;
    color: var(--paper);
    font-family: "Oswald", sans-serif;
    font-weight: 500;
    font-size: 26px;
    letter-spacing: 1px;
    text-transform: uppercase;
    white-space: nowrap;
  }
  .brand-square {
    width: 18px;
    height: 18px;
    background: currentColor;
    flex: none;
  }

  /* Front of card */
  .card-front { background: var(--paper); }
  .front-brand {
    position: absolute;
    left: 40px;
    top: 150px;
    width: 290px;
    display: flex;
    align-items: center;
    gap: 12px;
    color: var(--slate);
    font-family: "Oswald", sans-serif;
    font-weight: 500;
    font-size: 24px;
    letter-spacing: 0.5px;
    text-transform: uppercase;
    line-height: 1.15;
  }
  .divider {
    position: absolute;
    left: 352px;
    top: 70px;
    width: 2px;
    height: 190px;
    background: var(--slate);
  }
  .contact-block {
    position: absolute;
    left: 378px;
    top: 62px;
    color: var(--ink-soft);
  }
  .person-name {
    font-family: "Oswald", sans-serif;
    font-weight: 700;
    font-size: 34px;
    color: var(--slate);
    letter-spacing: 1px;
    line-height: 1.05;
  }
  .person-title {
    font-size: 16px;
    margin-bottom: 14px;
  }
  .contact-list { list-style: none; font-size: 14px; line-height: 1.45; }
  .contact-list li { display: flex; align-items: flex-start; gap: 9px; margin-bottom: 4px; }
  .contact-list svg { width: 13px; height: 13px; margin-top: 3px; flex: none; fill: var(--slate); }
  .footer-band { position: absolute; left: 0; bottom: 0; width: 665px; height: 62px; }
  .web-address {
    position: absolute;
    right: 28px;
    bottom: 14px;
    color: var(--paper);
    font-size: 15px;
    letter-spacing: 2.5px;
  }
</style>
</head>
<body>

  <section class="card card-back" aria-label="Card back">
    <div class="pattern-area" role="img" aria-label="Repeating brand mark pattern in glossy slate tones"></div>
    <div class="back-brand"><span class="brand-square"></span>Cedar Ridge Mechanical</div>
  </section>

  <section class="card card-front" aria-label="Card front">
    <div class="front-brand"><span class="brand-square"></span><span>Cedar Ridge Mechanical</span></div>
    <div class="divider"></div>

    <div class="contact-block">
      <h1 class="person-name">DANIEL HAYES</h1>
      <p class="person-title">Founder &amp; CEO</p>
      <ul class="contact-list">
        <li>
          <svg viewBox="0 0 24 24"><path d="M12 2a7 7 0 0 0-7 7c0 5 7 13 7 13s7-8 7-13a7 7 0 0 0-7-7zm0 9.5A2.5 2.5 0 1 1 12 6.5a2.5 2.5 0 0 1 0 5z"/></svg>
          <span>423 Street Address Here, City<br>State &amp; Country, ZIP Code</span>
        </li>
        <li>
          <svg viewBox="0 0 24 24"><path d="M6.6 10.8a15 15 0 0 0 6.6 6.6l2.2-2.2a1 1 0 0 1 1-.25 11.4 11.4 0 0 0 3.6.57 1 1 0 0 1 1 1V20a1 1 0 0 1-1 1A17 17 0 0 1 3 4a1 1 0 0 1 1-1h3.5a1 1 0 0 1 1 1c0 1.25.2 2.45.57 3.57a1 1 0 0 1-.25 1z"/></svg>
          <span>1-123-456-7890</span>
        </li>
        <li>
          <svg viewBox="0 0 24 24"><path d="M6.6 10.8a15 15 0 0 0 6.6 6.6l2.2-2.2a1 1 0 0 1 1-.25 11.4 11.4 0 0 0 3.6.57 1 1 0 0 1 1 1V20a1 1 0 0 1-1 1A17 17 0 0 1 3 4a1 1 0 0 1 1-1h3.5a1 1 0 0 1 1 1c0 1.25.2 2.45.57 3.57a1 1 0 0 1-.25 1z"/></svg>
          <span>123-456-7890</span>
        </li>
        <li>
          <svg viewBox="0 0 24 24"><path d="M7 1h10a2 2 0 0 1 2 2v18a2 2 0 0 1-2 2H7a2 2 0 0 1-2-2V3a2 2 0 0 1 2-2zm0 3v15h10V4z"/></svg>
          <span>123-456-7890</span>
        </li>
        <li>
          <svg viewBox="0 0 24 24"><path d="M2 5h20v14H2zm2 2v.5l8 5 8-5V7z"/></svg>
          <span>info@yourwebsitehere.com</span>
        </li>
      </ul>
    </div>

    <svg class="footer-band" viewBox="0 0 665 62" aria-hidden="true">
      <path d="M0 50 L0 40 L360 40 C380 40 385 2 410 2 L665 2 L665 12 L420 12 C395 12 390 50 370 50 Z" fill="var(--silver)"/>
      <path d="M0 62 L0 50 L370 50 C390 50 395 12 420 12 L665 12 L665 62 Z" fill="var(--slate)"/>
    </svg>
    <p class="web-address">www.yourwebsitehere.com</p>
  </section>

</body>
</html>
```